To design a brand identity that is simple and creative with 'Corvane' as the brand name, I like modern simple fonts like helvetica neue, I want to print both sides of the card, I am open to dark front and white back, but the design needs to transfer well to letter heads and email signatures, I am looking for sophisticated and elegant, but open minded about clever and off the wall, I do not do 'boring' Corvane Ventures is the mother company for a small group, specialising in Management & consulting, Software development and construction, we have a high level of integrity, we are transparent and accountable for what we do. my images are provided as a guide only, Im not expecting them to be just copied, Im looking for a creator and passionate thinker, who will put life into their work.

Target Market(s)

usually business minded people who are looking for something different in me, such as leadership, confidence and focus with thinking that is per haps a little outside the box..

Industry/Entity Type

Construction

Requirements
Must have
• clean, minmalistic
Nice to have
• custom logo
Should not have
• boring, traditional

```html
<!DOCTYPE html>
<html lang="en">
<head>
<meta charset="utf-8">
<title>Corvane Ventures – Business Card</title>
<link href="https://fonts.googleapis.com/css2?family=Open+Sans:wght@400;700&display=swap" rel="stylesheet">
<style>
  :root {
    --stage: #ecebe8;
    --card-dark: #050505;
    --card-light: #ffffff;
    --brand-orange: #f26a2b;
    --subline-grey: #8a8a8a;
    --name-gold: #f7b500;
    --contact-white: #ffffff;
    --service-red: #f0504a;
    --bullet-grey: #8c8c8c;
    --url-dark: #2b2b2b;
    --rule-grey: #9a9a9a;
    --grad-yellow: #ffb800;
    --grad-red: #ff2a1c;
    --grad-magenta: #b8226f;
    --grad-teal: #139e8c;
  }
  * { box-sizing: border-box; margin: 0; padding: 0; }
  html, body { width: 1200px; height: 720px; overflow: hidden; }
  body {
    background: var(--stage);
    font-family: "Open Sans", Arial, sans-serif;
    position: relative;
  }
  .card {
    position: absolute;
    top: 205px;
    width: 540px;
    height: 309px;
    border-radius: 4px;
    overflow: hidden;
    box-shadow: 0 6px 18px rgba(0,0,0,.18);
  }

  /* ---------- Front ---------- */
  .card--front { left: 50px; background: var(--card-dark); }
  .front__band {
    position: absolute;
    left: 0; right: 0; top: 152px; bottom: 0;
    background: linear-gradient(90deg, var(--grad-yellow) 0%, var(--grad-red) 25%, var(--grad-magenta) 58%, var(--grad-teal) 95%);
  }
  .front__band::after {
    content: "";
    position: absolute; inset: 0;
    background: linear-gradient(162deg, var(--card-dark) 0%, var(--card-dark) 42%, rgba(5,5,5,0) 72%);
  }
  .front__top-rule {
    position: absolute; left: 0; right: 0; top: 151px;
    height: 1px; background: var(--rule-grey); opacity: .7; z-index: 2;
  }
  .brand {
    position: absolute;
    display: flex; align-items: center; gap: 16px;
  }
  .brand__dot {
    width: 44px; height: 44px; border-radius: 50%;
    background: var(--brand-orange);
  }
  .brand__name {
    font-weight: 400;
    color: var(--brand-orange);
    line-height: 1;
  }
  .brand__subline {
    color: var(--subline-grey);
    font-size: 11px;
    letter-spacing: 3px;
    text-transform: uppercase;
    margin-top: 6px;
  }
  .card--front .brand { left: 150px; top: 46px; }
  .card--front .brand__name { font-size: 46px; }

  .holder {
    position: absolute; left: 0; right: 0; top: 172px; z-index: 3;
    text-align: center;
    color: var(--contact-white); font-size: 14px;
  }
  .holder__name { color: var(--name-gold); font-weight: 700; font-size: 16px; }
  .contact {
    position: absolute; left: 0; right: 0; top: 212px; z-index: 3;
    display: flex; align-items: center; justify-content: center;
    color: var(--contact-white); font-size: 12.5px; line-height: 1.6;
  }
  .contact__address { text-align: right; padding-right: 14px; }
  .contact__divider { width: 1px; height: 40px; background: rgba(255,255,255,.6); }
  .contact__lines { padding-left: 14px; }
  .contact__line { display: flex; align-items: center; gap: 6px; }
  .contact__icon { width: 11px; height: 11px; flex: none; }

  /* ---------- Back ---------- */
  .card--back { left: 610px; background: var(--card-light); }
  .card--back .brand { left: 120px; top: 62px; }
  .card--back .brand__name { font-size: 52px; }
  .card--back .brand__dot { width: 52px; height: 52px; }
  .services {
    position: absolute; left: 50px; right: 50px; top: 178px;
    list-style: none; display: flex; flex-wrap: wrap; justify-content: center;
    column-gap: 14px; row-gap: 4px;
    color: var(--service-red); font-size: 13px; text-transform: uppercase;
  }
  .services li::before {
    content: ""; display: inline-block; width: 5px; height: 5px;
    border-radius: 50%; background: var(--bullet-grey);
    margin-right: 5px; vertical-align: middle;
  }
  .website {
    position: absolute; left: 0; right: 0; top: 238px;
    text-align: center; color: var(--url-dark);
    font-size: 17px; letter-spacing: 4px;
  }
</style>
</head>
<body>

  <section class="card card--front" aria-label="Card front">
    <div class="front__band"></div>
    <div class="front__top-rule"></div>

    <div class="brand">
      <span class="brand__dot"></span>
      <div>
        <div class="brand__name">Corvane</div>
        <div class="brand__subline">Corvane Ventures</div>
      </div>
    </div>

    <p class="holder"><span class="holder__name">Your Name,</span> Title</p>

    <div class="contact">
      <div class="contact__address">Po Box 418<br>Kelmore 6031</div>
      <span class="contact__divider"></span>
      <div class="contact__lines">
        <div class="contact__line">
          <svg class="contact__icon" viewBox="0 0 12 12" aria-hidden="true">
            <circle cx="6" cy="6" r="5.3" fill="none" stroke="#f7b500" stroke-width="1.2"/>
            <path d="M4 3.2 L5 3 L5.6 4.6 L5 5.1 Q5.6 6.6 6.9 7 L7.4 6.4 L9 7 L8.8 8 Q6 8.6 4 5 Z" fill="#f7b500"/>
          </svg>
          +61 0400 512 907
        </div>
        <div class="contact__line">
          <svg class="contact__icon" viewBox="0 0 12 12" aria-hidden="true">
            <rect x="0.5" y="2" width="11" height="8" rx="1" fill="#f7b500"/>
            <path d="M1 2.6 L6 6.6 L11 2.6" fill="none" stroke="#000" stroke-width="0.9"/>
          </svg>
          Names@corvane.ventures
        </div>
      </div>
    </div>
  </section>

  <section class="card card--back" aria-label="Card back">
    <div class="brand">
      <span class="brand__dot"></span>
      <div>
        <div class="brand__name">Corvane</div>
        <div class="brand__subline">Corvane Ventures</div>
      </div>
    </div>

    <ul class="services">
      <li>Management &amp; Consulting</li>
      <li>Software Development</li>
      <li>Construction</li>
    </ul>

    <p class="website">www.corvane.com</p>
  </section>

</body>
</html>
```